Looking for a modern, Professional business card design

We have a simple business card, but are looking for a more modern, professional look. A sample of the basic card is attached as well as the logo. We would also like to add that we offer:
Struggling with your finances?
- Learn to become debt free
- Discover the power of cash
- Control your money instead of it controlling you
Let us help you achieve a new level of financial freedom!
Also, we would like to have a "SPECIAL OFFER!: FREE 30 minute consultation"
Financial Planning

```html
<!DOCTYPE html>
<html lang="en">
<head>
<meta charset="utf-8">
<title>Clearpath Financial Coaching – Business Card</title>
<link rel="stylesheet" href="https://fonts.googleapis.com/css2?family=Source+Sans+3:ital,wght@0,400;0,600;0,700;1,700&display=swap">
<style>
  :root {
    --page-bg: #ecebe8;
    --brand-green: #6cb043;
    --band-green: #5a9e3d;
    --deep-green: #3f8d2c;
    --band-text: #f3f1a6;
    --ink: #1d1d1b;
    --white: #ffffff;
    --card-shadow: 0 10px 28px rgba(0,0,0,0.18);
  }
  * { box-sizing: border-box; margin: 0; padding: 0; }
  html, body { width: 1200px; height: 900px; overflow: hidden; }
  body {
    background: var(--page-bg);
    font-family: "Source Sans 3", sans-serif;
    position: relative;
  }
  .card {
    position: absolute;
    width: 556px;
    height: 345px;
    box-shadow: var(--card-shadow);
    overflow: hidden;
  }

  /* Front */
  .card-front {
    left: 237px; top: 60px;
    background: var(--brand-green);
    color: var(--white);
  }
  .holder { position: absolute; left: 25px; top: 36px; }
  .holder-name { font-size: 19px; font-weight: 700; letter-spacing: 0.2px; }
  .holder-role { font-size: 15px; font-weight: 400; margin-top: 2px; }
  .brand-symbol-area {
    position: absolute;
    right: 0; top: 0;
    width: 320px; height: 345px;
    background: radial-gradient(ellipse at 62% 62%, #ffffff 0%, #ffffff 38%, #bfe08f 58%, var(--brand-green) 78%);
  }
  .contact-list {
    position: absolute; left: 25px; bottom: 26px;
    list-style: none; font-size: 15px; line-height: 20px;
  }
  .contact-list li { display: flex; align-items: center; gap: 8px; }
  .contact-list svg { width: 12px; height: 12px; fill: var(--white); flex: none; }

  /* Back */
  .card-back {
    left: 457px; top: 517px;
    width: 560px;
    background: var(--white);
    text-align: center;
  }
  .brand-lockup {
    display: flex; align-items: center; justify-content: center; gap: 12px;
    margin-top: 44px;
  }
  .brand-dot { width: 26px; height: 26px; border-radius: 50%; background: var(--brand-green); }
  .brand-name { font-size: 30px; font-weight: 700; color: var(--ink); letter-spacing: 0.5px; }
  .brand-tagline { font-size: 10px; color: #555; margin-top: 4px; }
  .headline-band {
    position: absolute; left: 0; right: 0; top: 138px; height: 42px;
    background: var(--band-green);
    color: var(--band-text);
    font-size: 17px; font-weight: 600; letter-spacing: 0.3px;
    line-height: 42px;
  }
  .benefits {
    position: absolute; left: 0; right: 0; top: 186px;
    list-style: none; font-size: 15.5px; line-height: 20px; color: var(--ink);
  }
  .benefits li::before { content: "➤"; color: var(--deep-green); margin-right: 8px; font-size: 13px; }
  .promise {
    position: absolute; left: 0; right: 0; top: 252px;
    font-size: 15px; font-weight: 700; font-style: italic; color: var(--deep-green);
  }
  .offer {
    position: absolute; left: 0; right: 0; top: 292px;
    font-size: 17px; font-weight: 700; color: var(--ink);
  }
  .offer-label { color: var(--deep-green); font-weight: 600; }
</style>
</head>
<body>

  <section class="card card-front">
    <div class="brand-symbol-area" role="img" aria-label="Brand symbol area in green and white"></div>
    <div class="holder">
      <p class="holder-name">Daniel R. Hayes</p>
      <p class="holder-role">Personal financial coach</p>
    </div>
    <ul class="contact-list">
      <li>
        <svg viewBox="0 0 24 24" aria-hidden="true"><path d="M6.6 10.8a15.1 15.1 0 0 0 6.6 6.6l2.2-2.2c.3-.3.7-.4 1-.2 1.1.4 2.3.6 3.6.6.6 0 1 .4 1 1V20c0 .6-.4 1-1 1A17 17 0 0 1 3 4c0-.6.4-1 1-1h3.5c.6 0 1 .4 1 1 0 1.3.2 2.5.6 3.6.1.3 0 .7-.2 1z"/></svg>
        (205) 555-0182
      </li>
      <li>
        <svg viewBox="0 0 24 24" aria-hidden="true"><path d="M2 5h20v14H2z M2 5l10 8 10-8" /></svg>
        daniel@steadyledgercoaching.com
      </li>
      <li>
        <svg viewBox="0 0 24 24" aria-hidden="true"><circle cx="12" cy="12" r="10"/></svg>
        www.steadyledgercoaching.com
      </li>
    </ul>
  </section>

  <section class="card card-back">
    <div class="brand-lockup">
      <span class="brand-dot"></span>
      <span class="brand-name">CLEARPATH FINANCIAL COACHING</span>
    </div>
    <p class="brand-tagline">Achieve a new level of personal freedom</p>
    <div class="headline-band">STRUGGLING WITH YOUR FINANCES?</div>
    <ul class="benefits">
      <li>Learn to become debt free</li>
      <li>Discover the power of cash</li>
      <li>Control your money instead of it controlling you</li>
    </ul>
    <p class="promise">Let us help you achieve a new level of financial freedom!</p>
    <p class="offer"><span class="offer-label">SPECIAL OFFER!:</span> FREE 30 MINUTE CONSULTATION</p>
  </section>

</body>
</html>
```